Hollow Thicket, a 3d voxel survival video game needs a card for gaming conventions

I am the lead developer for Hollow Thicket http://www.HollowThicket.example and need a business card to hand out at an indie gaming convention
The card would need to include the game name, website url, my name, position (Lead Developer), e-mail and phone number
The game is a 3d, voxel (with smooth terrain) based survival game with guns and wildlife. The main icon of the game would likely be a grizzly bear but I am willing to accept other designs too.
Attached is a media kit for the game with some images you can use but don't have to its just what little art I can provide. Anything on the website or from the video game can also be used. unrelated art can also be used.
Target Market(s)
Indie Developers/publishers at conferences
Industry/Entity Type
Games
Contact Information for Business Card
Name: Corin Waldrick
Position: Lead Developer
E-mail: Pale_Kettle@mailbox.example
Phone number: 555-372-1186

```html
<!DOCTYPE html>
<html lang="en">
<head>
<meta charset="utf-8">
<title>Hollow Thicket — Business Card</title>
<link rel="stylesheet" href="https://fonts.googleapis.com/css2?family=Arimo:wght@400;700&display=swap">
<style>
  :root {
    --page: #e9e6df;
    --card: #0d0d0d;
    --cream: #e6dab4;
    --red: #d4433a;
    --text-light: #d8d4c8;
    --photo-light: #d9d5c3;
    --photo-mid: #b9a98c;
    --photo-dark: #7a4a2c;
    --edge: #f4f4f2;
  }
  * { box-sizing: border-box; margin: 0; padding: 0; }
  html, body { width: 1200px; height: 858px; overflow: hidden; }
  body {
    background: var(--page);
    font-family: "Arimo", Arial, sans-serif;
    display: flex;
    flex-direction: column;
    align-items: center;
    justify-content: center;
    gap: 60px;
  }
  .card {
    position: relative;
    width: 560px;
    height: 320px;
    background: var(--card);
    border-radius: 4px;
    box-shadow: 0 8px 24px rgba(0,0,0,0.25);
    overflow: hidden;
  }
  .card-front .hero-photo {
    position: absolute;
    left: 0; top: 0;
    width: 250px; height: 320px;
  }
  .wordmark {
    font-weight: 700;
    text-transform: uppercase;
    color: var(--cream);
    letter-spacing: 0.12em;
  }
  .card-front .wordmark {
    position: absolute;
    left: 214px; top: 34px;
    font-size: 30px;
  }
  .identity {
    position: absolute;
    left: 232px; top: 96px;
  }
  .identity .person-name {
    color: var(--red);
    font-weight: 700;
    font-size: 18px;
    letter-spacing: 0.04em;
  }
  .identity .person-role {
    color: var(--text-light);
    font-weight: 700;
    font-size: 13px;
    margin-top: 5px;
    letter-spacing: 0.03em;
  }
  .contact-list {
    position: absolute;
    left: 300px; top: 212px;
    list-style: none;
    color: var(--text-light);
    font-size: 14px;
    letter-spacing: 0.04em;
  }
  .contact-list li {
    display: flex;
    align-items: center;
    gap: 8px;
    margin-bottom: 7px;
  }
  .contact-list svg { width: 12px; height: 12px; flex: none; }
  .card-back {
    display: flex;
    align-items: center;
    justify-content: center;
  }
  .card-back .wordmark {
    font-size: 46px;
  }
</style>
</head>
<body>
  <section class="card card-front">
    <svg class="hero-photo" viewBox="0 0 250 320" role="img" aria-label="Photograph of a roaring grizzly bear against a pale background">
      <defs>
        <radialGradient id="bearTone" cx="0.4" cy="0.5" r="0.6">
          <stop offset="0" stop-color="var(--photo-dark)"/>
          <stop offset="0.55" stop-color="var(--photo-mid)"/>
          <stop offset="1" stop-color="var(--photo-light)"/>
        </radialGradient>
      </defs>
      <path d="M0 0 H188 Q250 160 188 320 H0 Z" fill="url(#bearTone)"/>
      <path d="M188 0 Q250 160 188 320" fill="none" stroke="var(--edge)" stroke-width="7"/>
    </svg>

    <div class="wordmark">Hollow Thicket</div>

    <div class="identity">
      <p class="person-name">Corin Waldrick</p>
      <p class="person-role">Lead Developer</p>
    </div>

    <ul class="contact-list">
      <li>
        <svg viewBox="0 0 12 12" aria-hidden="true"><path d="M3 1 L5 3.5 L4 5 Q5 7 7 8 L8.5 7 L11 9 L9.5 11 Q4 10.5 1 3 Z" fill="var(--red)"/></svg>
        555-372-1186
      </li>
      <li>
        <svg viewBox="0 0 12 12" aria-hidden="true"><rect x="1" y="2.5" width="10" height="7" fill="var(--red)"/><path d="M1 2.5 L6 6.5 L11 2.5" fill="none" stroke="var(--card)" stroke-width="1"/></svg>
        Pale_Kettle@mailbox.example
      </li>
      <li>
        <svg viewBox="0 0 12 12" aria-hidden="true"><circle cx="6" cy="6" r="5" fill="none" stroke="var(--red)" stroke-width="1.4"/><ellipse cx="6" cy="6" rx="2" ry="5" fill="none" stroke="var(--red)" stroke-width="1"/><line x1="1" y1="6" x2="11" y2="6" stroke="var(--red)" stroke-width="1"/></svg>
        www.hollowthicket.example
      </li>
    </ul>
  </section>

  <section class="card card-back">
    <div class="wordmark">Hollow Thicket</div>
  </section>
</body>
</html>
```